"Harbor Builders" is a residential building company and needs a new business card design and may re

We would like a redesign based on the existing logo, and would like to see a new font as well. We are bespoke home builders who build sustainable energy efficient homes.

Industry/Entity Type

Construction

Contact Information for Business Card

Business card size 40mm x 90mm

Colors

Designer to choose colors to be used in the design.

```html
<!DOCTYPE html>
<html lang="en">
<head>
<meta charset="utf-8">
<title>Harbor Builders – Business Card</title>
<link rel="stylesheet" href="https://fonts.googleapis.com/css2?family=Roboto:wght@400;500;700&family=Roboto+Condensed:wght@700&display=swap">
<style>
  :root {
    --stage: #2a2a2a;
    --card-white: #f2f2f2;
    --lime: #bcd631;
    --ink: #1a1a1a;
    --text-grey: #4a4a4a;
    --soft-white: #f5f3f0;
  }
  * { box-sizing: border-box; margin: 0; padding: 0; }
  html, body { width: 1200px; height: 960px; overflow: hidden; }
  body {
    background: var(--stage);
    position: relative;
    font-family: "Roboto", Arial, sans-serif;
  }
  .card {
    position: absolute;
    width: 600px;
    height: 342px;
  }
  .card--front { left: 302px; top: 129px; background: var(--card-white); }
  .card--back  { left: 299px; top: 488px; background: var(--lime); }

  .brand {
    position: absolute;
    left: 31px; top: 38px;
    display: flex; align-items: center; gap: 10px;
  }
  .brand__square {
    width: 26px; height: 26px;
    background: var(--lime);
  }
  .brand__name {
    font-weight: 500;
    font-size: 27px;
    color: var(--ink);
    letter-spacing: -0.2px;
  }

  .holder {
    position: absolute;
    left: 30px; top: 123px;
    font-family: "Roboto Condensed", "Arial Narrow", sans-serif;
    font-weight: 700;
    font-size: 22px;
    color: var(--ink);
    letter-spacing: 0.1px;
  }
  .details {
    position: absolute;
    left: 31px; top: 159px;
    font-size: 15px;
    line-height: 18px;
    color: var(--text-grey);
  }
  .details__company { font-weight: 500; }
  .details__gap { margin-top: 3px; }

  .contacts {
    position: absolute;
    left: 32px; top: 256px;
    list-style: none;
    font-size: 15px;
    line-height: 19.5px;
    color: var(--text-grey);
  }
  .contacts li { display: flex; align-items: center; gap: 8px; }
  .contacts svg { width: 14px; height: 14px; fill: var(--ink); flex: none; }

  .feature-mark {
    position: absolute;
    left: 252px; top: 62px;
    width: 340px; height: 220px;
    display: flex; align-items: center; justify-content: center; gap: 20px;
  }
  .feature-mark__square {
    width: 84px; height: 84px;
    background: var(--lime);
    flex: none;
  }
  .feature-mark__name {
    font-weight: 700;
    font-size: 52px;
    line-height: 54px;
    color: var(--ink);
    letter-spacing: -0.5px;
  }

  .back-name {
    position: absolute;
    left: 0; right: 0; top: 136px;
    text-align: center;
    font-weight: 500;
    font-size: 44px;
    color: var(--soft-white);
  }
  .back-url {
    position: absolute;
    left: 0; right: 0; top: 297px;
    text-align: center;
    font-size: 14px;
    letter-spacing: 2.6px;
    color: var(--soft-white);
  }
</style>
</head>
<body>
  <section class="card card--front" aria-label="Business card front">
    <div class="brand">
      <span class="brand__square"></span>
      <span class="brand__name">harbor builders</span>
    </div>

    <h1 class="holder">DANIEL MORETTI</h1>

    <div class="details">
      <p class="details__company">Harbor Builders Pty Ltd</p>
      <p>PO Box 4120 Eastgate</p>
      <p>LPO Lakeview WA 6099</p>
      <p class="details__gap">Registration 40871</p>
      <p>ABN: 12 345 678 901</p>
    </div>

    <ul class="contacts">
      <li>
        <svg viewBox="0 0 14 14" aria-hidden="true"><path d="M4 0h6a1 1 0 0 1 1 1v12a1 1 0 0 1-1 1H4a1 1 0 0 1-1-1V1a1 1 0 0 1 1-1zm0.5 1.5v9.5h5V1.5zM7 11.6a0.8 0.8 0 1 0 0 1.6a0.8 0.8 0 0 0 0-1.6z"/></svg>
        <span>0400 555 018</span>
      </li>
      <li>
        <svg viewBox="0 0 14 14" aria-hidden="true"><path d="M1 3h12v1.2L7 8 1 4.2zM1 5.6l6 3.8 6-3.8V11H1z"/></svg>
        <span>daniel@harborbuilders.com.au</span>
      </li>
      <li>
        <svg viewBox="0 0 14 14" aria-hidden="true"><circle cx="7" cy="7" r="6"/><path d="M3 5q2-1 3 1t3 1M4 10q2-2 5-1" stroke="#f2f2f2" stroke-width="1.2" fill="none"/></svg>
        <span>www.harborbuilders.com.au</span>
      </li>
    </ul>

    <div class="feature-mark">
      <span class="feature-mark__square"></span>
      <span class="feature-mark__name">harbor<br>builders</span>
    </div>
  </section>

  <section class="card card--back" aria-label="Business card back">
    <p class="back-name">Harbor Builders</p>
    <p class="back-url">www.harborbuilders.com.au</p>
  </section>
</body>
</html>
```